Pediatric Speech Therapy Private Practice Announcement

I opened a solo private practice as a pediatric speech therapist in June 2014 in Orinda, CA in June 2014. I have 25 years experience in the field and worked as the Director of a very successful group practice of speech therapists in nearby Walnut Creek. I am trying to get my own name established in the local community and letting people know that I now have my own practice, which I call Dalworth Speech-Language Center.

I would like this postcard to advertise low-cost speech-language screenings offered to nearby preschools.

Target Market(s)

Preschool Directors

Requirements
Must have
• Photos of children, preschool ages, 3-5

Bright colors to get attention

```html
<!DOCTYPE html>
<html lang="en">
<head>
<meta charset="utf-8">
<title>Dalworth Speech-Language Center – Postcard</title>
<link rel="stylesheet" href="https://fonts.googleapis.com/css2?family=Jost:wght@300;400;700&family=Questrial&family=Roboto+Condensed:ital,wght@1,700&display=swap">
<style>
  :root {
    --backdrop: #5a5a5c;
    --paper: #ffffff;
    --magenta: #d6097b;
    --magenta-deep: #c8076f;
    --navy: #1f3a8a;
    --ink: #243a6b;
    --orange: #f0761e;
    --yellow: #fff200;
    --ring-yellow: #fde86a;
    --ring-orange: #fcc35b;
    --pink-soft: #eeaacb;
    --dot-pink: #e0428f;
    --dot-green: #6dbd45;
    --dot-blue: #33b7ea;
  }
  * { margin: 0; padding: 0; box-sizing: border-box; }
  html, body { width: 1200px; height: 815px; overflow: hidden; }
  body { background: var(--backdrop); position: relative; }

  .postcard {
    position: absolute; left: 60px; top: 60px; width: 1080px; height: 692px;
    background: var(--paper); overflow: hidden;
  }
  .postcard > * { position: absolute; }

  .headline {
    left: 43px; top: 28px; color: var(--magenta);
    font: 300 61px/1 "Jost", sans-serif; letter-spacing: 0.5px;
  }
  .headline .line { display: block; margin-bottom: 2px; }
  .headline .place {
    display: block; font-weight: 700; font-size: 44px; margin-top: 10px; letter-spacing: 1px;
  }
  .intro {
    left: 43px; top: 218px; width: 575px; color: var(--ink);
    font: 400 17.5px/1.3 "Jost", sans-serif;
  }

  .photo { display: block; }
  .photo-children {
    left: 0; top: 310px; width: 650px; height: 300px;
    background: radial-gradient(ellipse at 45% 55%, #f4c9a8 0%, #f2a25c 35%, #e9eef3 75%, #ffffff 100%);
    border-radius: 0 0 40% 40% / 0 0 25% 25%;
  }
  .photo-circle { border-radius: 50%; }
  .photo-story {
    left: 587px; top: -3px; width: 300px; height: 300px; border: 9px solid var(--ring-yellow);
    background: radial-gradient(circle at 60% 35%, #d9c9a0 0%, #9bb36a 40%, #6a4d3b 80%);
  }
  .photo-toybox {
    left: 775px; top: 170px; width: 330px; height: 330px; border: 9px solid var(--ring-orange);
    background: radial-gradient(circle at 40% 45%, #f4cdb6 0%, #f2a0b2 35%, #e3423e 70%, #c9a06a 100%);
  }
  .photo-blocks {
    left: 622px; top: 316px; width: 234px; height: 234px; border: 9px solid var(--ring-yellow);
    background: radial-gradient(circle at 50% 45%, #f7d6c5 0%, #ec9aa8 40%, #f1c33a 75%, #e9e2c9 100%);
  }

  .dot { border-radius: 50%; }
  .dot-pink-large { left: 538px; top: -15px; width: 70px; height: 70px; background: var(--pink-soft); }
  .dot-pink { left: 632px; top: 305px; width: 28px; height: 28px; background: var(--dot-pink); }
  .dot-green { left: 592px; top: 545px; width: 40px; height: 40px; background: var(--dot-green); }

  .offer {
    left: 890px; top: 20px; width: 190px; text-align: center; color: var(--navy);
    font-family: "Jost", sans-serif;
  }
  .offer-only { font-weight: 700; font-size: 21px; line-height: 1; margin-left: -38px; }
  .offer-price { color: var(--orange); font-weight: 700; font-size: 64px; line-height: 1; }
  .offer-price small { font-size: 36px; font-weight: 400; }
  .offer-label { font-size: 16px; line-height: 1.2; margin-top: 2px; }

  .cta-band { left: 0; top: 0; width: 1080px; height: 692px; }
  .cta {
    left: 712px; top: 562px; width: 355px; text-align: center;
  }
  .cta-phone {
    color: #fff; font: italic 700 38px/1 "Roboto Condensed", sans-serif;
  }
  .cta-note {
    color: var(--yellow); margin-top: 10px;
    font: italic 700 19px/1.1 "Roboto Condensed", sans-serif;
  }

  .practice-name {
    left: 0; top: 608px; width: 700px; text-align: center;
    font-family: "Questrial", sans-serif;
  }
  .practice-title { color: var(--navy); font-size: 33px; line-height: 1.1; }
  .practice-services { color: var(--magenta-deep); font-size: 19px; margin-top: 4px; }
</style>
</head>
<body>
<main class="postcard">
  <svg class="cta-band" viewBox="0 0 1080 692" aria-hidden="true">
    <path d="M684 692 C682 610 715 565 800 540 C880 518 1000 515 1080 468 L1080 692 Z" fill="var(--magenta)"/>
    <circle cx="875" cy="505" r="17" fill="var(--dot-blue)"/>
    <circle cx="1025" cy="510" r="32" fill="var(--yellow)"/>
  </svg>

  <span class="dot dot-pink-large"></span>

  <h1 class="headline">
    <span class="line">NEW PEDIATRIC</span>
    <span class="line">SPEECH THERAPY</span>
    <span class="place">PRACTICE IN ORINDA</span>
  </h1>

  <p class="intro">Dalworth Speech-Language Center, a new speech therapy practice in Orinda owned by Nora Whitfield, MS, CCC-SLP, is offering low cost ($40) on site speech-language screenings at preschools this Fall in the Lamorinda area.</p>

  <div class="photo photo-children" role="img" aria-label="Photo of four preschool children lying on the floor, resting their chins on their hands"></div>
  <div class="photo photo-circle photo-toybox" role="img" aria-label="Photo of a teacher and a young girl sorting building blocks from a red basket"></div>
  <div class="photo photo-circle photo-story" role="img" aria-label="Photo of a teacher reading a picture book to a group of preschoolers"></div>
  <div class="photo photo-circle photo-blocks" role="img" aria-label="Photo of a therapist building with colourful blocks alongside a little girl"></div>

  <span class="dot dot-pink"></span>
  <span class="dot dot-green"></span>

  <div class="offer">
    <p class="offer-only">ONLY</p>
    <p class="offer-price">40<small>$</small></p>
    <p class="offer-label">SPEECH-LANGUAGE<br>SCREENING</p>
  </div>

  <div class="cta">
    <p class="cta-phone">Call (925) 555-0142</p>
    <p class="cta-note">for additional information, or to<br>schedule an on-site screening at<br>your preschool today!</p>
  </div>

  <div class="practice-name">
    <p class="practice-title">Dalworth Speech-Language Center</p>
    <p class="practice-services">Speech, Language, and Social Communication Therapy Services</p>
  </div>
</main>
</body>
</html>
```